Web design project for exciting Australian start-up

Background
We are looking for a creative and talented web design artist to work alongside our market leading web developer.
• You will be required to create a modern and clean design theme for our website, incorporating selected rustic colour scheme elements for our exciting Australian start-up to operate within the coffee industry.
reoccurring work to be expected to flow to the successful designer.
Requirements
• c. 5 - 10 page website
• Landing page
• Log in/ out
• 404 template
• Typography is emphasised
• Please use either a) typemarrow.com, b) free web fonts, c) brindle fonts
• All design elements in vector format
• Preferably with icons for each header title(i.e. about us, how it works etc) but designer have free reign over how the site looks, so might not be applicable
• All pages to be responsive
• Down to eSlab resolution

High level visual design brief attached - additional pages to be worked from base design.

Design inspiration
• We would like to use design elements from the following sources:
http://www.zandrix.com/halcyon/ (Functionality)
Colour scheme refer to logo and complementary style guide

```html
<!DOCTYPE html>
<html lang="en">
<head>
<meta charset="utf-8">
<title>Brewhaven – Online Coffee Market Place</title>
<link rel="stylesheet" href="https://fonts.googleapis.com/css2?family=Oswald:wght@500;600;700&family=Roboto:wght@300;400&display=swap">
<style>
  :root {
    --bg-header: #f3f3f3;
    --bg-hero: #ffffff;
    --bg-footer: #ebebeb;
    --ink: #3a3a3a;
    --ink-soft: #6b6b6b;
    --line: #c9c9c9;
    --orange: #f7953a;
    --orange-deep: #e8701a;
    --red: #e8404a;
    --bean-dark: #4a2414;
    --bean-mid: #7a3a1e;
    --bean-light: #a4582e;
    --porcelain: #efebe7;
  }
  * { box-sizing: border-box; margin: 0; padding: 0; }
  html, body { width: 1200px; height: 988px; overflow: hidden; }
  body { font-family: "Roboto", Arial, sans-serif; color: var(--ink); background: var(--bg-hero); position: relative; }

  .site-header { position: absolute; inset: 0 0 auto 0; height: 97px; background: var(--bg-header); border-bottom: 1px solid var(--line); }
  .nav-btn { position: absolute; top: 33px; height: 30px; display: flex; align-items: center; justify-content: center; gap: 6px;
    font-size: 13px; text-transform: uppercase; color: var(--ink); background: #fff; border: 1px solid var(--line); border-radius: 2px; }
  .nav-btn--active { background: var(--orange); border-color: var(--orange); color: #fff; }
  .nav-btn--login { background: var(--red); border-color: var(--red); color: #fff; }
  .brand { position: absolute; top: 30px; left: 0; width: 1200px; display: flex; justify-content: center; align-items: center; gap: 10px; }
  .brand__name { font-family: "Oswald", Arial, sans-serif; font-weight: 700; font-size: 30px; letter-spacing: 2px; color: #2b2b2b; }
  .brand__dot { width: 22px; height: 22px; border-radius: 50%; background: var(--orange); }

  .hero { position: absolute; top: 98px; left: 0; width: 1200px; height: 691px; background: var(--bg-hero); overflow: hidden; }
  .hero__title { position: absolute; left: 70px; top: 136px; line-height: 1; }
  .hero__lead { display: block; font-weight: 300; font-size: 55px; letter-spacing: -2.5px; color: #444; }
  .hero__strong { display: block; font-family: "Oswald", Arial, sans-serif; font-weight: 600; font-size: 80px; letter-spacing: 0; color: var(--red); margin-top: -4px; }
  .hero__accent { display: block; font-family: "Oswald", Arial, sans-serif; font-weight: 600; font-size: 62px; color: var(--orange-deep); margin-top: -6px; }
  .video-btn { position: absolute; left: 70px; top: 347px; width: 188px; height: 42px; border: 1px solid #9a9a9a; background: rgba(255,255,255,.6);
    display: flex; align-items: center; padding-left: 22px; gap: 16px; font-family: "Oswald", Arial, sans-serif; font-weight: 500; font-size: 20px; color: #333; }
  .cup-photo { position: absolute; left: 686px; top: 116px; width: 464px; height: 344px;
    background: radial-gradient(ellipse at 50% 50%, var(--porcelain) 0%, #f6f3f0 55%, rgba(255,255,255,0) 72%); }
  .beans-photo { position: absolute; left: 0; top: 420px; width: 1200px; height: 271px;
    background: linear-gradient(180deg, rgba(255,255,255,0) 0%, var(--bean-light) 22%, var(--bean-mid) 50%, var(--bean-dark) 100%); }

  .site-footer { position: absolute; top: 789px; left: 0; width: 1200px; height: 199px; background: var(--bg-footer); }
  .footer-col { position: absolute; top: 35px; }
  .footer-col h3 { font-size: 14px; font-weight: 400; text-transform: uppercase; color: #222; margin-bottom: 14px; }
  .footer-col p { width: 302px; font-size: 11.5px; font-weight: 300; line-height: 17px; color: var(--ink-soft); }
  .footer-col li { list-style: none; font-size: 13.5px; font-weight: 300; color: #444; line-height: 20px; }
  .social li { display: flex; align-items: center; gap: 9px; line-height: 27px; }
  .social-dot { width: 17px; height: 17px; border-radius: 50%; background: #9a9a9a; }
  .footer-brand { position: absolute; left: 961px; top: 62px; display: flex; align-items: center; gap: 8px; }
  .footer-brand .brand__name { font-size: 22px; color: #5e5e5e; }
  .footer-brand .brand__dot { width: 16px; height: 16px; background: #9a9a9a; }
  .copyright { position: absolute; left: 961px; top: 116px; font-size: 13px; font-weight: 300; color: #444; }
</style>
</head>
<body>
  <header class="site-header">
    <a class="nav-btn nav-btn--active" style="left:52px;width:86px">Home</a>
    <a class="nav-btn" style="left:147px;width:85px">About us</a>
    <div class="brand"><span class="brand__dot"></span><span class="brand__name">BREWHAVEN</span></div>
    <a class="nav-btn" style="left:942px;width:114px">How it works</a>
    <a class="nav-btn nav-btn--login" style="left:1065px;width:84px">
      <svg width="13" height="13" viewBox="0 0 13 13" aria-hidden="true"><circle cx="6.5" cy="3.5" r="3" fill="#fff"/><path d="M1 13c0-4 2.5-5.5 5.5-5.5S12 9 12 13z" fill="#fff"/></svg>Login</a>
  </header>

  <section class="hero">
    <h1 class="hero__title">
      <span class="hero__lead">AUSTRALIA’S FIRST</span>
      <span class="hero__strong">ONLINE COFFEE</span>
      <span class="hero__accent">MARKET PLACE</span>
    </h1>
    <a class="video-btn"><svg width="13" height="14" viewBox="0 0 13 14" aria-hidden="true"><path d="M0 0L13 7L0 14z" fill="var(--red)"/></svg>WATCH VIDEO</a>
    <div class="cup-photo" role="img" aria-label="White cup of coffee with crema on a saucer, a few roasted beans beside it"></div>
    <div class="beans-photo" role="img" aria-label="Pile of roasted coffee beans spread across the width of the page"></div>
  </section>

  <footer class="site-footer">
    <div class="footer-col" style="left:51px">
      <h3>About us</h3>
      <p>Lorem ipsum dolor sit amet, consectetur adipisicing elit, sed do eiusmod tempor incididunt ut labore et dolore magna aliqua. Ut enim ad minim veniam, quis nostrud exercitation ullamco laboris nisi ut aliquip ex ea commodo consequat. Duis aute irure dolor in reprehenderit in voluptate velit esse cillum dolore eu fugiat nulla pariatur.</p>
    </div>
    <div class="footer-col" style="left:428px">
      <h3>Helpful info</h3>
      <ul><li>About us</li><li>Media Enquiries</li><li>Terms &amp; Conditions</li><li>Privacy Policy</li></ul>
    </div>
    <div class="footer-col" style="left:618px">
      <h3>Who we are</h3>
      <ul><li>How It Works</li><li>Faq</li><li>Contact Us</li></ul>
    </div>
    <div class="footer-col social" style="left:788px">
      <h3 style="margin-bottom:6px">Follow us</h3>
      <ul>
        <li><span class="social-dot"></span>Friendloop</li>
        <li><span class="social-dot"></span>Worknest</li>
        <li><span class="social-dot"></span>Friendloop</li>
        <li><span class="social-dot"></span>Worknest</li>
      </ul>
    </div>
    <div class="footer-brand"><span class="brand__dot"></span><span class="brand__name">BREWHAVEN</span></div>
    <p class="copyright">Copyright © 2014 Brewhaven.</p>
  </footer>
</body>
</html>
```